business card deign

Logo needs the following on it.
1. attached logo
2. Tagline - "From frosty coolers to late night tunes...we bring it all!"
3. Name- Dalton Pikes, Founder and CPO
4. Address - 412 E. Carver Avenue, Ste 2207, Cedar Bay, CB. 33917
5. Phone - 555.318.4726

```html
<!DOCTYPE html>
<html lang="en">
<head>
<meta charset="utf-8">
<title>Brightkeg Business Card</title>
<link rel="stylesheet" href="https://fonts.googleapis.com/css2?family=Montserrat:wght@400;600;700&display=swap">
<style>
  :root {
    --backdrop: #8e8e8e;
    --card-light: #ededed;
    --card-dark: #141414;
    --ink: #111111;
    --ink-soft: #5a5a5a;
    --rule: #6e6e6e;
    --foil: #bdbdbd;
  }
  * { margin: 0; padding: 0; box-sizing: border-box; }
  html, body {
    width: 1188px; height: 1200px; overflow: hidden;
    background: var(--backdrop);
    font-family: "Montserrat", sans-serif;
  }
  .card {
    position: absolute; left: 245px; width: 696px; height: 385px;
  }
  .card-front { top: 160px; background: var(--card-light); }
  .card-back { top: 627px; background: var(--card-dark); }

  .brand-name {
    position: absolute; font-weight: 700; letter-spacing: 0.18em; white-space: nowrap;
  }
  .card-front .brand-name {
    left: 70px; width: 240px; top: 240px; text-align: center;
    font-size: 22px; color: var(--ink);
  }
  .card-back .brand-name {
    left: 0; width: 100%; top: 238px; text-align: center;
    font-size: 30px; color: var(--foil);
  }
  .divider {
    position: absolute; left: 328px; top: 109px; width: 1px; height: 166px;
    background: var(--rule);
  }
  .contact {
    position: absolute; left: 361px; top: 108px; color: var(--ink-soft);
    font-size: 16.5px; line-height: 1.35; white-space: nowrap;
  }
  .contact .person {
    font-weight: 700; font-size: 21px; color: var(--ink); line-height: 1.1;
  }
  .contact .role { margin-top: 3px; }
  .contact .lines { margin-top: 20px; list-style: none; }
  .contact .lines li { display: flex; align-items: center; gap: 9px; height: 24px; }
  .contact .lines svg { width: 18px; height: 15px; fill: var(--ink); flex: none; }
  .contact .address { margin-top: 8px; line-height: 1.38; }
  .tagline {
    position: absolute; left: 0; width: 100%; top: 323px; text-align: center;
    font-size: 17px; color: var(--ink-soft); white-space: nowrap;
  }
</style>
</head>
<body>
  <section class="card card-front">
    <div class="brand-name">BRIGHTKEG</div>
    <div class="divider"></div>
    <div class="contact">
      <div class="person">DALTON PIKES</div>
      <div class="role">Founder and CPO</div>
      <ul class="lines">
        <li>
          <svg viewBox="0 0 18 15" aria-hidden="true"><path d="M1 5c0-3 16-3 16 0v1h-4V4.5H5V6H1z"/><path d="M4 7h10l2 7H2z"/><circle cx="9" cy="10.5" r="2.2" fill="#ededed"/></svg>
          <span>555.318.4726</span>
        </li>
        <li>
          <svg viewBox="0 0 18 15" aria-hidden="true"><path d="M1 2h16v2L9 9 1 4z"/><path d="M1 6l8 5 8-5v7H1z"/></svg>
          <span>hello@brightkeg.com</span>
        </li>
      </ul>
      <div class="address">412 E. Carver Avenue,<br>Ste 2207, Cedar Bay, CB. 33917</div>
    </div>
    <p class="tagline">From frosty coolers to late night tunes...we bring it all!</p>
  </section>

  <section class="card card-back">
    <div class="brand-name">BRIGHTKEG</div>
  </section>
</body>
</html>
```